New profile page for existing party website

For the party website 'Partyvenz' we need a new design for the user profile page.

The page should show
* a profile picture
* basic information like name, age and city
* music styles he/she likes
* links to their Chatterbook profile and website
* a bio (HTML content)
* events they plan to go to
* past events
* pictures

Challenge is that some users may have little information (just their name) while others have a huge description, lots of foto's, events, etc.

Please visit http://www.partyvenz.example and http://www.partyvenz.example/users/bertil

Target Market(s)

Men and women between 18 and 35

Industry/Entity Type

Night Club

Number of Pages Required

2 page

Font styles to use
Other font styles liked:
• Roboto

Requirements
Must have
• Please design how the page looks with a fully filled out profile and with an empty profile.
• It should fit well with the existing website.
• Include designs for both for small screens (mobile) and large screens (tablet, desktop).
Nice to have
• UX design on how to collapse or paginate sections.
• Interactive effects would be a bonus.
Should not have
• The page should not have subnavigation like menus or tabs.

```html
<!DOCTYPE html>
<html lang="nl">
<head>
<meta charset="utf-8">
<title>Partyvenz – Profiel</title>
<link rel="stylesheet" href="https://fonts.googleapis.com/css2?family=Open+Sans:wght@400;600;700&display=swap">
<style>
:root{
  --black:#050505;
  --dark:#262626;
  --darker:#1c1c1c;
  --white:#ffffff;
  --text:#222222;
  --muted:#8a8a8a;
  --light:#efefef;
  --footer-text:#a8a8a8;
  --hero-a:#2b2f2c;
  --hero-b:#5a3a36;
  --video-a:#3c4a36;
  --video-b:#6f7566;
}
*{box-sizing:border-box;margin:0;padding:0}
html,body{width:1200px;height:2426px;overflow:hidden}
body{font-family:"Open Sans",Arial,sans-serif;color:var(--text);background:var(--white);position:relative}
.abs{position:absolute}

/* header */
.site-header{position:absolute;top:0;left:0;width:1200px;height:91px;background:var(--black)}
.brand{position:absolute;left:99px;top:24px;color:var(--white);font-size:34px;font-weight:700;letter-spacing:1px}
.nav{position:absolute;top:38px;left:0;list-style:none}
.nav li{position:absolute;color:var(--white);font-size:12.5px;white-space:nowrap;letter-spacing:.5px}
.search{position:absolute;left:872px;top:31px;width:115px;height:34px;border:1px solid #555;border-radius:3px;color:#ccc;font-size:11px;padding:9px 7px;background:var(--black)}
.account{position:absolute;left:1003px;top:31px;width:98px;height:34px;background:var(--white);color:#111;border-radius:3px;font-size:12px;font-weight:600;text-align:center;line-height:34px}

/* hero */
.hero{position:absolute;top:91px;left:0;width:1200px;height:396px;background:linear-gradient(100deg,var(--hero-a),#3d2c2a 30%,#3a3834 55%,var(--hero-b) 80%,#2e2b28);color:var(--white);text-align:center}
.hero-shade{position:absolute;inset:0;background:rgba(0,0,0,.45)}
.avatar{position:absolute;left:516px;top:28px;width:168px;height:168px;border-radius:50%;border:4px solid var(--white);background:radial-gradient(circle at 50% 40%,#a07a5e,#6a4c3c 60%,#3a2d28)}
.hero-name{position:absolute;top:222px;width:100%;font-size:29px;font-weight:400;letter-spacing:.5px}
.hero-meta{position:absolute;width:100%;font-size:12.5px;font-weight:700;letter-spacing:.3px}
.hero-social{position:absolute;top:337px;left:567px;display:flex;gap:9px}
.hero-social span{width:29px;height:29px;border-radius:50%;background:var(--white)}
.chev{position:absolute;top:180px}

/* content sections */
.section{position:absolute;left:0;width:1200px;text-align:center}
.section h2{font-size:29px;font-weight:400;letter-spacing:.5px}
.section h3{font-size:21px;font-weight:400}
.section p{font-size:12.3px;line-height:26px;margin:0 auto}
.bio{top:487px;height:223px}
.past{top:710px;height:293px;background:linear-gradient(180deg,var(--dark),var(--darker));color:var(--white)}
.event{position:absolute;top:98px;width:300px}
.event h4{font-size:18.5px;font-weight:400;margin-bottom:12px}
.event p{font-size:12px;line-height:22px}
.event .date{margin-top:10px;font-size:14px}
.info{top:1003px;height:265px}
.video{position:absolute;top:1268px;left:0;width:1200px;height:317px;background:linear-gradient(180deg,#6f7566 0%,#59614f 32%,var(--video-a) 60%,#2d3828)}
.join{top:1585px;height:189px}

/* lower grid */
.lower{position:absolute;top:1774px;left:0;width:1200px;height:372px;background:var(--light)}
.lower h2{position:absolute;top:42px;font-size:25px;font-weight:400;color:#1a1a1a}
.pager{position:absolute;top:48px;display:flex;gap:5px}
.pager span{width:15px;height:15px;border-radius:50%;background:#d0d0d0}
.thumb{position:absolute;border:3px solid var(--white);box-shadow:0 0 3px rgba(0,0,0,.25)}
.plan-title{position:absolute;left:267px;font-size:17px;color:#222}
.plan-text{position:absolute;left:267px;width:320px;font-size:11px;line-height:20px;color:var(--muted)}
.plan-more{position:absolute;left:267px;font-size:11px;color:#222;text-decoration:underline}

/* footer */
.footer{position:absolute;top:2146px;left:0;width:1200px;height:280px;background:var(--darker);color:var(--footer-text)}
.footer-brand{position:absolute;left:99px;top:80px;font-size:36px;font-weight:700;color:#8c8c8c}
.footer h5{position:absolute;top:30px;font-size:17px;font-weight:400;color:#d0d0d0;letter-spacing:.5px}
.footer p,.footer li{font-size:12px;line-height:21px}
.contact-line{position:absolute;left:391px;display:flex;align-items:center;gap:14px;font-size:12px}
.newsletter-input{position:absolute;left:686px;top:118px;width:184px;height:39px;background:#111;color:#777;font-size:10.5px;padding:12px 12px}
.newsletter-btn{position:absolute;left:870px;top:118px;width:79px;height:39px;background:#4a4a4a;color:var(--white);font-size:13px;font-weight:700;text-align:center;line-height:39px}
.social-list{position:absolute;left:1012px;top:68px;list-style:none}
.social-list li{display:flex;align-items:center;gap:14px;margin-bottom:7px;font-size:12px}
.social-list li span{width:7px;height:9px;background:var(--footer-text)}
.copyright{position:absolute;top:2386px;width:1200px;text-align:center;font-size:12px;color:var(--white)}
.corner{position:absolute;top:2386px;left:1150px;font-size:12px;color:var(--white)}
</style>
</head>
<body>

<header class="site-header">
  <div class="brand">Partyvenz</div>
  <ul class="nav">
    <li style="left:390px">HOME</li>
    <li style="left:474px">AGENDA</li>
    <li style="left:572px">FREE TICKETS</li>
    <li style="left:697px">PHOTOS</li>
    <li style="left:794px">NEWS</li>
  </ul>
  <div class="search">Zoeken</div>
  <div class="account">MY ACCOUNT</div>
</header>

<section class="hero">
  <div class="hero-shade" role="img" aria-label="Blurred party photo background"></div>
  <svg class="chev" style="left:52px" width="18" height="38" viewBox="0 0 18 38"><path d="M16 2 2 19l14 17" fill="none" stroke="#888" stroke-width="2"/></svg>
  <svg class="chev" style="left:1130px" width="18" height="38" viewBox="0 0 18 38"><path d="M2 2l14 17L2 36" fill="none" stroke="#888" stroke-width="2"/></svg>
  <div class="avatar" role="img" aria-label="Profile photo of the member"></div>
  <h1 class="hero-name">RUDIK PHOTOGRAPHY</h1>
  <div class="hero-meta" style="top:272px">MEMBER SINCE : JANUARY 1, 2006 &nbsp;&nbsp;&nbsp;/&nbsp;&nbsp;&nbsp; AGE : 34 &nbsp;&nbsp;&nbsp;/&nbsp;&nbsp;&nbsp; CITY : AMERSFOORT &nbsp;&nbsp;&nbsp;/&nbsp;&nbsp;&nbsp; MUSIC : LATIN &nbsp;&nbsp;&nbsp;/&nbsp;&nbsp;&nbsp; SALSA</div>
  <div class="hero-meta" style="top:304px">ACTIVE SINCE: JAN 2006 &nbsp;&nbsp;SHOOTS: 500 AND COUNTING</div>
  <div class="hero-social"><span aria-label="Chatterbook"></span><span aria-label="Chirpwave"></span></div>
</section>

<section class="section bio">
  <h2 style="margin-top:33px">BIO</h2>
  <h3 style="margin-top:10px">Wil jij fotograferen voor Partyvenz?</h3>
  <p style="width:1100px;margin-top:6px">Als je uitgaan leuk vindt, makkelijk bent in de omgang en uiteraard houdt van fotograferen, biedt Partyvenz je de kans een kijkje te nemen in de wereld van de partyfotografie. Door de inzet van de fotografen is Partyvenz uitgegroeid tot een van de meest toonaangevende partysites van Nederland. De betrouwbaarheid, de hoge kwaliteit van de foto's en het coveren van de belangrijkste evenementen maakt van Partyvenz een van de best bezochte websites in ons vakgebied.</p>
</section>

<section class="section past">
  <h2 style="margin-top:30px">PAST EVENTS</h2>
  <svg class="abs" style="left:34px;top:128px" width="18" height="38" viewBox="0 0 18 38"><path d="M16 2 2 19l14 17" fill="none" stroke="#666" stroke-width="2"/></svg>
  <svg class="abs" style="left:1150px;top:128px" width="18" height="38" viewBox="0 0 18 38"><path d="M2 2l14 17L2 36" fill="none" stroke="#666" stroke-width="2"/></svg>
  <div class="event" style="left:101px"><h4>VELVET, CLUB NORA, AMSTERDAM</h4><p>On the other hand, we denounce with righteous indig-nation and dislike men who are so beguiled and demor-alized by the charms of pleasure of the moment, so blinded by desire, that they the pain and trouble,..</p><div class="date">24 april 2015</div></div>
  <div class="event" style="left:450px"><h4>VELVET, CLUB NORA, AMSTERDAM</h4><p>On the other hand, we denounce with righteous indig-nation and dislike men who are so beguiled and demor-alized by the charms of pleasure of the moment, so blinded by desire, that they the pain and trouble,..</p><div class="date">24 april 2015</div></div>
  <div class="event" style="left:799px"><h4>VELVET, CLUB NORA, AMSTERDAM</h4><p>On the other hand, we denounce with righteous indig-nation and dislike men who are so beguiled and demor-alized by the charms of pleasure of the moment, so blinded by desire, that they the pain and trouble,..</p><div class="date">24 april 2015</div></div>
</section>

<section class="section info">
  <h2 style="margin-top:28px">BELANGRIJK INFORMATIE</h2>
  <h3 style="margin-top:8px">Fotograferen voor Partyvenz is op vrijwillige basis</h3>
  <p style="width:1110px;margin-top:2px">Je kan kiezen waar en wanneer je uitgaat en foto's maakt, maar een vaste inbreng word wel van je verwacht. Hoe meer je voor Partyvenz doet, hoe meer ervaring je opdoet met de camera en hoe beter je word. Hierdoor kan je weer naar interessantere feesten en festivals. Wat je wel krijgt is gratis entree voor een evenement en soms ook andere voordelen zoals gratis drankjes... Je gaat meestal met ze tweetjes op pad en ontmoet veel nieuwe mensen zoals DJ's en organisatoren. Hoe meer je voor Partyvenz.nl werkt hoe meer ervaring je er ook uit zal halen. De beste fotografen doen de leukste en de meest uitdagende evenementen bijvoorbeeld: Nightglow, Tropic Outdoor,<br>Sunrise weekend, Lagoon Dance etc.</p>
</section>

<div class="video" role="img" aria-label="Video still of a crowd at an outdoor festival">
  <svg class="abs" style="left:581px;top:139px" width="38" height="38" viewBox="0 0 38 38"><circle cx="19" cy="19" r="19" fill="#bbb" opacity=".85"/><path d="M15 11v16l12-8z" fill="#444"/></svg>
</div>

<section class="section join">
  <h2 style="margin-top:28px">AANMELDEN</h2>
  <h3 style="margin-top:4px">Wil jij ook het team van Partyvenz</h3>
  <p style="width:1110px;margin-top:2px">Versterken en het nachtleven van een andere kant verkennen? Geef je dan op, stuur een mailtje naar rudi@partyvenz.example Vermeld daar goed in je naam, leeftijd, woonplaats en het type camera dat je hebt en je ervaring op het gebied van fotograferen.</p>
</section>

<section class="lower">
  <h2 style="left:99px">EVENTS THEY PLAN TO GO TO</h2>
  <div class="pager" style="left:550px"><span></span><span></span></div>
  <h2 style="left:621px">PICTURES</h2>
  <div class="pager" style="left:1072px"><span></span><span></span></div>

  <div class="thumb" role="img" aria-label="Event photo" style="left:99px;top:97px;width:148px;height:100px;background:linear-gradient(135deg,#5c3b3a,#a8766a,#3b2b33)"></div>
  <div class="plan-title" style="top:96px">Nam libero tempore</div>
  <div class="plan-text" style="top:128px">At vero eos et accusamus et iusto odio dignissimos ducimus qui blanditiis praesentium voluptatum deleniti atque</div>
  <div class="plan-more" style="top:176px">LEARN MORE ...</div>

  <div class="thumb" role="img" aria-label="Event photo" style="left:99px;top:225px;width:148px;height:101px;background:linear-gradient(180deg,#8c9fb8,#5f6b72 55%,#3a3a3a)"></div>
  <div class="plan-title" style="top:224px">Nam libero tempore</div>
  <div class="plan-text" style="top:256px">At vero eos et accusamus et iusto odio dignissimos ducimus qui blanditiis praesentium voluptatum deleniti atque</div>
  <div class="plan-more" style="top:304px">LEARN MORE ...</div>

  <div class="thumb" role="img" aria-label="Party photo" style="left:621px;top:97px;width:149px;height:100px;background:linear-gradient(135deg,#d9a04a,#b77246,#e3c07a)"></div>
  <div class="thumb" role="img" aria-label="Party photo" style="left:788px;top:97px;width:148px;height:100px;background:linear-gradient(135deg,#9a9a8a,#c8753a,#6d6d60)"></div>
  <div class="thumb" role="img" aria-label="Party photo" style="left:953px;top:97px;width:147px;height:100px;background:linear-gradient(135deg,#6b4e3a,#b9783e,#4a3b32)"></div>
  <div class="thumb" role="img" aria-label="Party photo" style="left:621px;top:226px;width:149px;height:100px;background:linear-gradient(135deg,#2e2622,#c26a2c,#3a2e28)"></div>
  <div class="thumb" role="img" aria-label="Party photo" style="left:788px;top:226px;width:148px;height:100px;background:linear-gradient(135deg,#4a4a4a,#d7772d,#5a5048)"></div>
  <div class="thumb" role="img" aria-label="Party photo" style="left:953px;top:226px;width:147px;height:100px;background:linear-gradient(135deg,#2a2624,#6a4a3a,#1e1b1a)"></div>
</section>

<footer class="footer">
  <div class="footer-brand">Partyvenz</div>

  <h5 style="left:391px">CONTACT US</h5>
  <p class="abs" style="left:391px;top:62px;width:250px;font-size:12.5px">On the other hand, we denounce with righteous indignatio</p>
  <div class="contact-line" style="top:118px">
    <svg width="18" height="16" viewBox="0 0 18 16"><path d="M3 1c1 0 2 2 3 3.5L5 6c1 2 3 4 5 5l1.5-1c1.5 1 3.5 2 3.5 3 0 1-2 2.5-3 2.5C6 15.5 1.5 10 1.5 4 1.5 3 2.5 1 3 1z" fill="none" stroke="#a8a8a8" stroke-width="1.2"/></svg>
    <span>+111 1111 111</span>
  </div>
  <div class="contact-line" style="top:144px">
    <svg width="18" height="14" viewBox="0 0 18 14"><rect x="1" y="1" width="16" height="12" fill="none" stroke="#a8a8a8" stroke-width="1.2"/><path d="M1 1l8 7 8-7" fill="none" stroke="#a8a8a8" stroke-width="1.2"/></svg>
    <span>info@partyvenz.example</span>
  </div>

  <h5 style="left:686px">NEWSLETTER</h5>
  <p class="abs" style="left:686px;top:62px;width:270px;font-size:10.5px;line-height:19px">Excepteur sint occaecat cupidatat non proident, sunt in culpa qui officia deserunt mollit anim</p>
  <div class="newsletter-input">Enter your email address</div>
  <div class="newsletter-btn">SIGN UP</div>

  <h5 style="left:1012px;top:22px">SOCIAL</h5>
  <ul class="social-list">
    <li><span></span>Chatterbook</li>
    <li><span></span>Chirpwave</li>
    <li><span></span>Circlespace</li>
    <li><span></span>Clipstream</li>
  </ul>
</footer>
<div class="copyright">© 2016 © 2004 - 2016 Partyvenz All right receved</div>
<div class="corner">C1</div>

</body>
</html>
```